Heritage Hollow Business Cards

Require a business card design. <br/><br/>Needs to include logo (either round or long version) plus these details:<br/>Maya Torvell<br/>Heritage Hollow<br/>maya@kelvadtrading.com.au<br/>02 6481 7395<br/>PO Box Glenwarra NSW 2791<br/>www.heritagehollow.com.au<br/><br/>I need in an editable format so that I can create for multiple staff members. <br/><br/>

Target Market(s)

We are an online store selling renovation products to home owners are builders. Looking for a classic classy design.

Industry/Entity Type

Home And Garden

Contact Information for Business Card

Maya Torvell
Heritage Hollow
maya@kelvadtrading.com.au
02 6481 7395
PO Box Glenwarra NSW 2791
www.heritagehollow.com.au

Colors

Designer to choose colors to be used in the design.

Requirements
Must have
• Must include Logo.

```html
<!DOCTYPE html>
<html lang="en">
<head>
<meta charset="utf-8">
<title>Heritage Hollow Business Cards</title>
<link rel="stylesheet" href="https://fonts.googleapis.com/css2?family=Lora:wght@400;600;700&display=swap">
<style>
  :root {
    --page: #d9d9d9;
    --ink: #2b2829;
    --paper: #ffffff;
    --light-text: #f1f1f1;
    --muted-text: #cfcfcf;
    --divider: #e6e6e6;
  }
  * { margin: 0; padding: 0; box-sizing: border-box; }
  html, body { width: 1200px; height: 880px; overflow: hidden; }
  body {
    background: var(--page);
    font-family: "Lora", Georgia, serif;
    position: relative;
  }
  .card {
    position: absolute;
    left: 260px;
    width: 680px;
    height: 389px;
    border-radius: 24px;
    overflow: hidden;
    box-shadow: 0 6px 18px rgba(0,0,0,0.18);
  }
  /* Back side */
  .card-back { top: 30px; background: var(--ink); }
  .back-brand {
    position: absolute;
    top: 120px; left: 0; right: 0;
    display: flex; align-items: center; justify-content: center; gap: 18px;
  }
  .brand-ring {
    width: 64px; height: 64px; border-radius: 50%;
    border: 1.5px solid var(--light-text);
  }
  .back-brand .brand-name {
    color: var(--light-text); font-weight: 600; font-size: 36px;
  }
  .back-web {
    position: absolute; bottom: 58px; left: 0; right: 0;
    text-align: center; color: var(--muted-text);
    font-size: 15px; letter-spacing: 5px;
  }
  /* Front side */
  .card-front { top: 461px; background: var(--paper); }
  .front-brand {
    position: absolute; top: 58px; left: 0; right: 0;
    display: flex; align-items: center; justify-content: center; gap: 16px;
  }
  .front-brand .brand-ring { border-color: var(--ink); width: 60px; height: 60px; }
  .front-brand .brand-name { color: var(--ink); font-weight: 600; font-size: 38px; }
  .contact-band {
    position: absolute; top: 160px; left: 0; right: 0; height: 160px;
    background: var(--ink);
  }
  .person {
    position: absolute; right: 372px; top: 50px; text-align: right;
  }
  .person-name { color: var(--light-text); font-weight: 700; font-size: 20px; }
  .person-title { color: var(--muted-text); font-size: 14px; margin-top: 4px; }
  .band-divider {
    position: absolute; left: 326px; top: 26px; width: 1px; height: 108px;
    background: var(--divider);
  }
  .contact-list {
    position: absolute; left: 344px; top: 32px; list-style: none;
  }
  .contact-list li {
    display: flex; align-items: center; gap: 8px;
    color: var(--light-text); font-size: 14.5px; height: 32px;
  }
  .contact-list svg { width: 18px; height: 18px; flex: none; }
  .front-web {
    position: absolute; bottom: 22px; left: 0; right: 0;
    text-align: center; color: var(--ink);
    font-size: 16px; letter-spacing: 7px;
  }
</style>
</head>
<body>

<section class="card card-back" aria-label="Business card back">
  <div class="back-brand">
    <span class="brand-ring"></span>
    <span class="brand-name">Heritage Hollow</span>
  </div>
  <p class="back-web">www.heritagehollow.com.au</p>
</section>

<section class="card card-front" aria-label="Business card front">
  <div class="front-brand">
    <span class="brand-ring"></span>
    <span class="brand-name">Heritage Hollow</span>
  </div>

  <div class="contact-band">
    <div class="person">
      <p class="person-name">Maya Torvell</p>
      <p class="person-title">Managing Director</p>
    </div>
    <span class="band-divider"></span>
    <ul class="contact-list">
      <li>
        <svg viewBox="0 0 18 18" aria-hidden="true"><circle cx="9" cy="9" r="8" fill="none" stroke="#f1f1f1" stroke-width="1.2"/><path d="M6.2 5.2l1.4-.3.8 1.9-.9.7c.5 1 1.2 1.7 2.1 2.2l.7-.9 1.9.8-.3 1.4c-3.3.1-5.8-2.5-5.7-5.8z" fill="#f1f1f1"/></svg>
        02 6481 7395
      </li>
      <li>
        <svg viewBox="0 0 18 18" aria-hidden="true"><circle cx="9" cy="9" r="8" fill="none" stroke="#f1f1f1" stroke-width="1.2"/><rect x="5" y="6" width="8" height="6" fill="none" stroke="#f1f1f1" stroke-width="1"/><path d="M5 6l4 3.2L13 6" fill="none" stroke="#f1f1f1" stroke-width="1"/></svg>
        maya@kelvadtrading.com.au
      </li>
      <li>
        <svg viewBox="0 0 18 18" aria-hidden="true"><circle cx="9" cy="9" r="8" fill="none" stroke="#f1f1f1" stroke-width="1.2"/><path d="M9 13.5s-3-3.2-3-5.4a3 3 0 016 0c0 2.2-3 5.4-3 5.4z" fill="none" stroke="#f1f1f1" stroke-width="1"/><circle cx="9" cy="8" r="1" fill="#f1f1f1"/></svg>
        PO Box Glenwarra NSW 2791
      </li>
    </ul>
  </div>

  <p class="front-web">www.heritagehollow.com.au</p>
</section>

</body>
</html>
```